Bold, Modern, Clean "Kestrelwaymassage.com" website

Why we stand out?
We are a male and female mobile massage team. Our names are Paul and Lina. 
Kestrel Way is a Seattle based mobile massage service. Our massage is offered to the community with a goal of facilitating balance within each individual. We specialize in integrated Pain management, and sports/medical massage therapy. Every client's first assessment is attended by our male and female massage therapist team. Depending on the goals identified for an individual determines which therapist will be assigned to provide treatment, if not both.

Our passion...
Here at Kestrel Way, we have a great passion for Postural Resoration and how it is integrated into an individual's Massage treatment. We pride ourselves in being natural facilitators of healing, which takes the ego of the therapist out of the client's healing process. We strive to deliver the best massage possible by including modalities such as Neuromuscular, Myofascial release, spontaneous muscle release, postural restoration, orthopedic, and medical massage.

Our education...

We are both Graduates of Venmora, school of massage therapy. We have continuing education in medical massage, myofacial release, trigger point therapy, postural restoration, anatomy, and spontaneous muscle release. Lina is also a Certified Yoga Instructor, which amplifies her experience with flexibility and strength as it pertains to each individual. Paul's passion is Massage, stretching, and strength training to encourage postural restoration and realignment.

Our rates-

Our rates are $75/ 60 minutes, $95/ 90 minutes, and $120/ 120 minutes.

Education-
Both Lina and I worked as behavioral health professionals that specialized in life skills mentoring for youth who had experienced different types of trauma. This led us both to want to help others in a different environment, where individuals can be empowered to take responsibility over their own healing. To us, massage is a type of manipulation physical therapy, that encourages healing on many levels.

Advice to any massage client-
The most important thing to 'us', as Licenced providers is to get you on to our table to show you our skills. But a good therapist never forgets that it's not about what we do for you, but what we can facilitate for you. Your health and healing has nothing to do with us. It is yours, not ours. Identify what your goals are with any Therapist, and know what the end looks like. Progress should be tangible, such as range of motion, and decreased pain.

Lina and Paul at Kestrel Way are awesome! I recently had open heart surgery, and Lina worked on me to increase my range of motion while helping with the pinched nerve from my arm being in the same position for so long during my surgery. My wife drives a lot for work, and Paul has helped decrease her neck and lower back pain immensely. They are seriously the best therapists I have ever worked with. I would recommend them to anyone who needs anything from stress relief to a medical massage treatment. They are professional, up beat, easy going, and always on time. And, I love that they meet us where ever we like! We did a staycation recently, where they came to our hotel to give us relaxation massages. Although usually they come to our home, where we focus on pain related issues. We will continue to work with them for a long, long time.

Target Market(s)

Mobile massage therapy clients

Industry/Entity Type

Massage Therapy

Coding

Coded - Design and coding required

Number of Pages Required

1 page

Font styles to use
Serif
Sans Serif

Requirements
Must have
• Please add or remove any information that would help the presentation of our website. Our logo is posted below, please include into the website.
• Please include a contact field that includes, kestrelwaymassage@fernmail.net,
• (206) 555-0148
• We have also included our own stock photos, as well as a photo of Paul and Lina. Please include a cropped photo of both massage therapists.

```html
<!DOCTYPE html>
<html lang="en">
<head>
<meta charset="utf-8">
<title>Kestrel Way Mobile Massage</title>
<link rel="stylesheet" href="https://fonts.googleapis.com/css2?family=Raleway:wght@400;500;600;700&family=Open+Sans:wght@400;600;700&display=swap">
<style>
:root{
  --navy:#232d6e;
  --blue:#1a8fc7;
  --dark:#231f20;
  --grey-bg:#e4e4e4;
  --text:#555a60;
  --muted:#8a8a8a;
  --white:#ffffff;
}
*{margin:0;padding:0;box-sizing:border-box}
html,body{width:1200px;height:2546px;overflow:hidden}
body{position:relative;background:var(--white);font-family:"Open Sans",Arial,sans-serif;color:var(--text)}
a{color:inherit;text-decoration:none}

/* Header */
.site-header{position:absolute;left:0;top:0;width:1200px;height:180px}
.nav-band{position:absolute;left:0;top:106px;width:1200px;height:70px;background:var(--navy);border-bottom:4px solid #d9dce8}
.brand{position:absolute;left:48px;top:24px;display:flex;align-items:center;gap:16px}
.brand-mark{width:58px;height:58px;border-radius:50%;background:var(--navy)}
.brand-name{font-family:"Raleway",sans-serif;font-weight:700;font-size:30px;color:var(--navy);white-space:nowrap}
.main-nav{position:absolute;top:106px;left:0;height:70px;width:1200px;font-size:11px;font-weight:600;color:var(--white)}
.main-nav a{position:absolute;top:30px;white-space:nowrap}
.main-nav a.active{color:var(--blue)}
.contact-chip{position:absolute;top:30px;display:flex;align-items:center;gap:10px}
.chip-icon{width:38px;height:38px;border-radius:50%;border:2px solid var(--blue);display:flex;align-items:center;justify-content:center}
.chip-label{display:block;font-size:11px;color:var(--blue);line-height:1.2}
.chip-value{font-size:17px;color:#666}
.chip-value.small{font-size:13px}

/* Hero */
.hero{position:absolute;left:0;top:180px;width:1200px;height:563px;background:linear-gradient(100deg,#4f3a30 0%,#8a6856 38%,#a88a76 65%,#cbbdb2 100%)}
.hero-title{position:absolute;left:50px;top:198px;font-family:"Raleway",sans-serif;font-weight:600;font-size:68px;color:var(--white);letter-spacing:1px}
.hero-copy{position:absolute;left:52px;top:280px;width:610px;font-size:14px;font-weight:600;color:var(--white);line-height:1.5}
.btn{display:inline-block;background:var(--blue);color:var(--white);font-size:12.5px;font-weight:600;text-align:center}
.hero-btn{position:absolute;left:50px;top:344px;width:130px;height:46px;line-height:46px}
.dots{position:absolute;display:flex;gap:10px}
.dot{width:14px;height:14px;border-radius:50%;background:var(--white)}
.dot.on{background:var(--navy)}

/* Services */
.services{position:absolute;left:0;top:743px;width:1200px;height:279px;background:var(--dark);border-top:3px solid #ddd}
.service{position:absolute;top:0;width:260px;text-align:center}
.service-photo{position:absolute;top:-68px;left:46px;width:168px;height:168px;border-radius:50%;border:4px solid var(--white)}
.service-title{margin-top:125px;font-family:"Raleway",sans-serif;font-weight:600;font-size:16px;color:var(--white)}
.service-title.accent{color:var(--blue)}
.service-copy{margin:8px auto 0;width:220px;font-size:12.5px;line-height:1.4;color:#8e8e8e}
.service-more{margin-top:12px;font-size:11.5px;font-weight:600;color:var(--white)}
.service-more.accent{color:var(--blue)}

/* Welcome + feed */
.section-heading{font-family:"Raleway",sans-serif;font-weight:500;font-size:22px;color:#111}
.section-heading span{color:var(--navy)}
.welcome{position:absolute;left:46px;top:1065px;width:580px}
.welcome p{margin-top:22px;font-size:12px;line-height:1.75;color:var(--muted)}
.welcome .btn{margin-top:24px;width:113px;height:38px;line-height:38px;font-size:11.5px}
.feed{position:absolute;left:674px;top:1068px;width:476px}
.feed-all{position:absolute;right:2px;top:18px;font-size:11px;font-weight:600;color:var(--navy)}
.feed-item{position:absolute;left:6px;width:464px;height:90px;border-bottom:2px dotted #cfcfcf}
.feed-thumb{position:absolute;left:0;top:0;width:103px;height:82px;background:linear-gradient(135deg,#f2c2a8,#c7765a)}
.feed-date{position:absolute;left:122px;top:0;font-size:11px;color:var(--muted)}
.feed-title{position:absolute;left:122px;top:16px;font-family:"Raleway",sans-serif;font-weight:600;font-size:16px;color:#111}
.feed-copy{position:absolute;left:122px;top:40px;width:340px;font-size:11.5px;line-height:1.45;color:#555}

/* Feature band */
.feature{position:absolute;left:0;top:1344px;width:1200px;height:382px;background:linear-gradient(90deg,#33231a 0%,#5c4231 35%,#7d6352 60%,#a69a90 100%)}
.feature-title{position:absolute;left:0;width:1200px;top:100px;text-align:center;font-family:"Raleway",sans-serif;font-size:70px;font-weight:400;color:var(--white)}
.feature-copy{position:absolute;left:160px;width:880px;top:212px;text-align:center;font-size:13.5px;line-height:1.65;color:var(--white)}

/* Testimonials */
.testimonials-heading{position:absolute;left:0;top:1772px;width:1200px;text-align:center;font-family:"Raleway",sans-serif;font-size:32px;font-weight:500;color:#111}
.testimonials-heading span{color:var(--navy)}
.quote-mark{position:absolute;font-family:Georgia,serif;font-size:60px;color:var(--navy);font-weight:700;line-height:1}
.testimonial-card{position:absolute;left:129px;top:1873px;width:920px;height:150px;border:1px solid #dcdcdc;border-radius:4px;background:var(--white)}
.avatar{position:absolute;left:34px;top:20px;width:110px;height:110px;border-radius:50%;border:3px solid #ddd;background:linear-gradient(160deg,#e9edf2,#9aa4b1)}
.testimonial-text{position:absolute;left:172px;top:42px;width:700px;font-size:14px;line-height:1.5;color:#555}
.testimonial-name{position:absolute;right:56px;top:110px;font-size:17px;font-weight:700;color:var(--navy)}
.ring-dots{position:absolute;left:579px;top:2081px;display:flex;gap:6px}
.ring{width:12px;height:12px;border-radius:50%;border:1.5px solid var(--navy)}
.ring.on{background:var(--navy)}

/* Footer */
.footer-panels{position:absolute;left:0;top:2152px;width:1200px;height:275px;background:var(--grey-bg)}
.footer-col{position:absolute;top:40px}
.footer-col+.footer-col{border-left:1px solid #cfcfcf}
.footer-title{font-family:"Raleway",sans-serif;font-weight:600;font-size:17px;color:var(--navy)}
.footer-copy{font-size:11.5px;line-height:1.5;color:#555}
.footer-btn{display:block;background:var(--navy);color:var(--white);font-size:11.5px;font-weight:600;text-align:center}
.email-field{width:298px;height:36px;border:1px solid #ddd;background:var(--white);font-size:10.5px;color:#aaa;padding:11px 12px}
.loc-row{position:relative;padding-left:26px;font-size:12px;line-height:1.5;color:#555;margin-bottom:6px}
.loc-row svg{position:absolute;left:0;top:3px}
.site-footer{position:absolute;left:0;top:2427px;width:1200px;height:119px;background:var(--navy);color:var(--white)}
.legal{position:absolute;top:24px;width:1200px;text-align:center;font-size:11px;font-weight:600}
.social{position:absolute;top:58px;left:496px;display:flex;gap:12px}
.social span{width:32px;height:32px;border-radius:50%;border:1.5px solid var(--white)}
</style>
</head>
<body>

<header class="site-header">
  <div class="nav-band"></div>
  <div class="brand"><span class="brand-mark"></span><span class="brand-name">Kestrel Way</span></div>

  <div class="contact-chip" style="left:726px">
    <span class="chip-icon"><svg width="18" height="18" viewBox="0 0 24 24"><path d="M6.6 10.8a15.1 15.1 0 006.6 6.6l2.2-2.2c.3-.3.7-.4 1-.2 1.1.4 2.3.6 3.6.6.6 0 1 .4 1 1V20c0 .6-.4 1-1 1A17 17 0 013 4c0-.6.4-1 1-1h3.5c.6 0 1 .4 1 1 0 1.3.2 2.5.6 3.6.1.3 0 .7-.2 1z" fill="none" stroke="#1a8fc7" stroke-width="1.8"/></svg></span>
    <span><span class="chip-label">Call Us</span><span class="chip-value">1234-567-890</span></span>
  </div>
  <div class="contact-chip" style="left:935px">
    <span class="chip-icon"><svg width="18" height="18" viewBox="0 0 24 24"><rect x="3" y="6" width="18" height="12" rx="1" fill="none" stroke="#1a8fc7" stroke-width="1.8"/><path d="M3 7l9 6 9-6" fill="none" stroke="#1a8fc7" stroke-width="1.8"/></svg></span>
    <span><span class="chip-label">EMAIL ID</span><span class="chip-value small">info@companyname.com</span></span>
  </div>

  <nav class="main-nav">
    <a class="active" style="left:251px">HOME</a>
    <a style="left:322px">WHY WE STAND OUT?</a>
    <a style="left:473px">OUR PASSIONOUR</a>
    <a style="left:602px">EDUCATION</a>
    <a style="left:701px">OUR RATES</a>
    <a style="left:799px">5/5 STARS MASSAGE THERAPY</a>
    <a style="left:991px">TESTIMONIALS</a>
    <a style="left:1103px">CONTACT</a>
  </nav>
</header>

<section class="hero" role="img" aria-label="Photo of a therapist giving a back and shoulder massage">
  <h1 class="hero-title">BODY MASSAGE</h1>
  <p class="hero-copy">Lorem ipsum dolor sit amet, consectetur adipiscing elit, sed do eiusmod tempor incidi-dunt ut labore et dolore magna aliqua. Ut enim ad minim veniam</p>
  <a class="btn hero-btn">READ MORE</a>
  <div class="dots" style="left:58px;top:519px"><span class="dot on"></span><span class="dot"></span><span class="dot"></span></div>
</section>

<section class="services">
  <div class="service" style="left:289px">
    <div class="service-photo" role="img" aria-label="Photo of a woman relaxing during a massage" style="background:linear-gradient(150deg,#a893b4,#4d3e64)"></div>
    <h3 class="service-title">Integrated Pain Management</h3>
    <p class="service-copy">Lorem ipsum dolor sit amet, consectetur ipsum dolor sit amet, consectetur adipis do edit</p>
    <p class="service-more">MORE &#9656;</p>
  </div>
  <div class="service" style="left:747px">
    <div class="service-photo" role="img" aria-label="Photo of a client receiving a facial and head massage" style="background:linear-gradient(150deg,#5e3520,#e0b795)"></div>
    <h3 class="service-title accent">Sports/Medical Massage Therapy</h3>
    <p class="service-copy">Lorem ipsum dolor sit amet, consectetur ipsum dolor sit amet, consectetur adipis do edit</p>
    <p class="service-more accent">MORE &#9656;</p>
  </div>
</section>

<section class="welcome">
  <h2 class="section-heading">WELCOME TO <span>KESTREL WAY MOBILE MASSAGE</span></h2>
  <p>Lorem ipsum dolor sit amet, consectetur adipiscing elit, sed do eiusmod tempor incididunt ut labore et dolore magna aliqua. Ut enim ad minim veniam, quis nostrud exercitation ullamco laboris nisi ut aliquip ex ea commodo consequat. Duis aute irure dolor in reprehenderit in voluptate velit esse cillum dolore eu fugiat nulla pariatur. Excepteur sint occaecat cupidatat non proident, sunt in culpa qui officia deserunt mollit anim id est laborum.</p>
  <a class="btn">READ MORE</a>
</section>

<section class="feed">
  <h2 class="section-heading">LATEST <span>FEED</span></h2>
  <a class="feed-all">View All</a>
  <div class="feed-item" style="top:44px">
    <div class="feed-thumb" role="img" aria-label="Photo of hands massaging a back"></div>
    <span class="feed-date">12/08/2015</span>
    <h4 class="feed-title">Lorem Ipsum Dolor Sit</h4>
    <p class="feed-copy">Lorem ipsum dolor sit amet, consectetur adipiscing elit, sed do eiusmod tempor incididunt ut labore</p>
  </div>
  <div class="feed-item" style="top:146px">
    <div class="feed-thumb" role="img" aria-label="Photo of hands massaging a shoulder"></div>
    <span class="feed-date">12/08/2015</span>
    <h4 class="feed-title">Lorem Ipsum Dolor Sit</h4>
    <p class="feed-copy">Lorem ipsum dolor sit amet, consectetur adipiscing elit, sed do eiusmod tempor incididunt ut labore</p>
  </div>
</section>

<section class="feature" role="img" aria-label="Photo of a client receiving a head massage">
  <h2 class="feature-title">HEAD MASSAGE</h2>
  <p class="feature-copy">Lorem ipsum dolor sit amet, consectetur adipiscing elit, sed do eiusmod tempor incididunt ut labore et dolore magna aliqua. Ut enim ad minim veniam, quis nostrud exercitation ullamco laboris nisi ut aliquip ex ea commodo consequat.</p>
</section>

<h2 class="testimonials-heading">Our <span>Testimonials</span></h2>
<span class="quote-mark" style="left:132px;top:1828px">&ldquo;</span>
<div class="testimonial-card">
  <div class="avatar" role="img" aria-label="Portrait of the reviewer"></div>
  <p class="testimonial-text">Lorem ipsum dolor sit amet, consectetur adipiscing elit, sed do eiusmod tempor incididunt ut labore et dolore magna aliqua. Ut enim ad minim veniam, quis nostrud exercitation ullamco laboris nisi ut aliquip ex ea commodo consequat.</p>
  <span class="testimonial-name">- Owen Hale</span>
</div>
<span class="quote-mark" style="left:1020px;top:2040px">&rdquo;</span>
<div class="ring-dots"><span class="ring"></span><span class="ring on"></span><span class="ring"></span></div>

<section class="footer-panels">
  <div class="footer-col" style="left:52px;width:360px">
    <h3 class="footer-title">ABOUT US</h3>
    <p class="footer-copy" style="margin-top:18px">Lorem ipsum dolor sit amet, consectetur adipiscing elit, sed do eiusmod tempor incididunt ut labore et dolore magna aliqua. Ut enim ad minim veniam, quis nostrud exercitation ullamco laboris nisi ut aliquip ex ea commodo consequat. Duis aute irure dolor in reprehenderit in voluptate velit esse cillum dolore eu fugiat nulla pariatur.</p>
    <a class="footer-btn" style="margin-top:26px;width:125px;height:38px;line-height:38px">READ MORE</a>
  </div>
  <div class="footer-col" style="left:467px;top:22px;height:230px;padding:18px 0 0 55px;width:420px">
    <h3 class="footer-title">NEWSLETTER SIGNUP</h3>
    <p class="footer-copy" style="margin-top:16px;width:310px">Subscribe our newsletter to know our daily updates and offer daily updates and offerpsum dolor sit amet elit, sed aliqua.</p>
    <div class="email-field" style="margin-top:14px">Enter your Email Id</div>
    <a class="footer-btn" style="margin-top:8px;width:298px;height:36px;line-height:36px;font-size:13px">SUBSCRIBE</a>
  </div>
  <div class="footer-col" style="left:886px;top:22px;height:230px;padding:18px 0 0 52px;width:314px">
    <h3 class="footer-title" style="margin-left:6px">LOCATION</h3>
    <div style="margin-top:20px">
      <div class="loc-row"><svg width="10" height="13" viewBox="0 0 10 13"><path d="M5 0a5 5 0 015 5c0 3.5-5 8-5 8S0 8.5 0 5a5 5 0 015-5z" fill="#232d6e"/><circle cx="5" cy="5" r="1.8" fill="#e4e4e4"/></svg>Company Name<br>Address Line 1, Address Line 2<br>Country - 123456</div>
      <div class="loc-row"><svg width="11" height="11" viewBox="0 0 24 24"><path d="M6.6 10.8a15.1 15.1 0 006.6 6.6l2.2-2.2c.3-.3.7-.4 1-.2 1.1.4 2.3.6 3.6.6.6 0 1 .4 1 1V20c0 .6-.4 1-1 1A17 17 0 013 4c0-.6.4-1 1-1h3.5c.6 0 1 .4 1 1 0 1.3.2 2.5.6 3.6.1.3 0 .7-.2 1z" fill="#232d6e"/></svg>Office: (206) 555-0148</div>
      <div class="loc-row"><svg width="11" height="9" viewBox="0 0 11 9"><rect width="11" height="9" fill="#232d6e"/><path d="M0 0l5.5 4.5L11 0" fill="none" stroke="#e4e4e4"/></svg>kestrelwaymassage@fernmail.net</div>
    </div>
  </div>
</section>

<footer class="site-footer">
  <p class="legal">About Us &nbsp;/&nbsp; Privacy Policy &nbsp;/&nbsp; Terms of Service &nbsp;/&nbsp; Contact Us</p>
  <div class="social" aria-label="Social media links"><span></span><span></span><span></span><span></span><span></span></div>
</footer>

</body>
</html>
```